VELMOR Website Design

We need a website designed for our company VELMOR. We are a luxury lifestyle club that will provide benefits and services for our members. The site should be clean & sleek, preferably using black and white (or darker colors). (example sites: stravenhall.example, plinth.example)

Here is a link of a sample page I did using wix. (https://dunmere7.sitehostly.example/mysite) This can be used to get a general idea.

Target Market(s)

Upper Middle Class in the United States

Number of Pages Required

5+ page

Font styles to use
Sans Serif
Other font styles liked:
• Arial (or other similar fonts)

Requirements
Must have
• A clean design that is eye-catching and speaks to our company.
Nice to have
• Ideas for copy.

```html
<!DOCTYPE html>
<html lang="en">
<head>
<meta charset="utf-8">
<title>VELMOR — Contact</title>
<link rel="stylesheet" href="https://fonts.googleapis.com/css2?family=Mulish:ital,wght@0,200;0,300;0,400;0,600;1,300&family=Arimo:wght@400;700&display=swap">
<style>
  :root {
    --black: #000000;
    --white: #ffffff;
    --ghost: #3a3a3a;
    --mist: #bdbdbd;
    --rule: #cfcfcf;
    --hero-dark: #0c0f1c;
    --hero-mid: #2b3146;
    --hero-light: #dcdad4;
    --sky: #3f86c9;
    --sea: #1f5c8f;
    --berry: #b5302a;
  }
  * { box-sizing: border-box; margin: 0; padding: 0; }
  html, body { width: 1077px; height: 1200px; overflow: hidden; background: var(--black); }
  body { position: relative; font-family: "Arimo", Arial, sans-serif; color: var(--white); }
  .abs { position: absolute; }

  /* header */
  .site-header { left: 0; top: 0; width: 1077px; height: 39px; background: var(--white); }
  .brand { left: 16px; top: 9px; font-family: "Mulish", sans-serif; font-weight: 400; font-size: 17px; color: var(--black); letter-spacing: 0.3px; }
  .nav { font-family: "Mulish", sans-serif; font-size: 5.6px; color: #333; top: 16px; letter-spacing: 0.2px; }
  .nav-active { left: 1030px; top: 14px; width: 32px; height: 11px; background: var(--black); color: var(--white); font-size: 5.6px; font-family: "Mulish", sans-serif; display: flex; align-items: center; justify-content: center; }
  .nav-pointer { left: 1039px; top: 33px; }

  /* hero */
  .hero { left: 0; top: 39px; width: 1077px; height: 474px;
    background: linear-gradient(100deg, var(--hero-light) 0%, #b9b8b2 30%, var(--hero-mid) 45%, var(--hero-dark) 65%, #35373f 85%, #9a9ea6 100%); }
  .hero-top { left: 0; top: 39px; width: 1077px; height: 8px; background: var(--black); }
  .dot { top: 487px; width: 7px; height: 7px; border-radius: 50%; background: rgba(255,255,255,0.75); }

  /* title band */
  .title-band { left: 0; top: 513px; width: 1077px; height: 91px; background: var(--black); overflow: hidden; }
  .title-word { left: 0; width: 1077px; bottom: -27px; text-align: center; font-family: "Mulish", sans-serif; font-weight: 200; font-size: 128px; line-height: 1; letter-spacing: 38px; padding-left: 38px; color: var(--ghost); }
  .subtitle-strip { left: 0; top: 604px; width: 1077px; height: 56px; background: var(--white); }
  .subtitle { width: 1077px; top: 12px; left: 0; text-align: center; font-family: "Mulish", sans-serif; font-style: italic; font-weight: 300; font-size: 28px; color: var(--mist); }

  /* contact */
  .envelope { left: 45px; top: 710px; }
  .contact-heading { left: 75px; width: 274px; top: 728px; text-align: center; font-family: "Mulish", sans-serif; font-weight: 400; font-size: 26px; letter-spacing: 0.5px; }
  .contact-tagline { left: 50px; width: 324px; top: 775px; text-align: center; font-family: "Mulish", sans-serif; font-style: italic; font-weight: 300; font-size: 14px; }
  .field { border: 1px solid var(--white); font-size: 8px; padding-left: 11px; display: flex; align-items: center; }
  .send { left: 125px; top: 1013px; width: 157px; height: 22px; border: 2px solid var(--white); display: flex; align-items: center; justify-content: center; font-weight: 700; font-size: 11px; letter-spacing: 0.3px; }

  .feature-photo { left: 436px; top: 710px; width: 589px; height: 325px;
    background: linear-gradient(180deg, var(--sky) 0%, #5e9bd0 40%, var(--sea) 58%, #d9dde2 80%, var(--berry) 100%); }
  .feature-quote { right: 52px; top: 1000px; font-family: "Arimo", Arial, sans-serif; font-style: italic; font-size: 20px; color: var(--white); }

  /* footer */
  .footer-rule { left: 0; top: 1088px; width: 1077px; height: 1px; background: var(--rule); }
  .footer-brand { left: 174px; top: 1122px; font-family: "Mulish", sans-serif; font-weight: 400; font-size: 17px; }
  .footer-copy { left: 187px; top: 1157px; font-size: 5.5px; }
  .footer-link { font-size: 7.5px; }
  .social-mark { width: 6px; height: 6px; border-radius: 50%; background: var(--white); }
  .newsletter-label { left: 512px; top: 1122px; font-size: 7.5px; }
  .newsletter-input { left: 512px; top: 1143px; width: 118px; height: 22px; border: 1px solid var(--white); font-size: 6.5px; padding-left: 11px; display: flex; align-items: center; }
  .newsletter-ok { left: 630px; top: 1143px; width: 33px; height: 22px; background: var(--white); color: var(--black); font-size: 6px; display: flex; align-items: center; justify-content: center; }
  .address-line { left: 795px; font-size: 6.5px; }
</style>
</head>
<body>
  <header class="abs site-header">
    <div class="abs brand">VELMOR</div>
    <div class="abs nav" style="left:811px">HOME</div>
    <div class="abs nav" style="left:854px">ABOUT</div>
    <div class="abs nav" style="left:902px">SERVICES &amp; BENEFITS</div>
    <div class="abs nav" style="left:989px">APPLY</div>
    <div class="abs nav-active">CONTACT</div>
  </header>

  <div class="abs hero" role="img" aria-label="Smiling man in a suit at the wheel of a luxury car with white leather seats"></div>
  <div class="abs hero-top"></div>
  <svg class="abs nav-pointer" width="14" height="7" viewBox="0 0 14 7"><polygon points="0,7 7,0 14,7" fill="#000"/></svg>
  <div class="abs dot" style="left:521px"></div>
  <div class="abs dot" style="left:536px"></div>
  <div class="abs dot" style="left:551px"></div>

  <section class="abs title-band"><div class="abs title-word">CONTACT</div></section>
  <div class="abs subtitle-strip"><div class="abs subtitle">A Members Only Lifestyle Club</div></div>

  <svg class="abs envelope" width="28" height="21" viewBox="0 0 28 21" fill="none" stroke="#fff" stroke-width="1.2">
    <rect x="0.6" y="0.6" width="26.8" height="19.8"/>
    <polyline points="0.6,0.6 14,12 27.4,0.6"/>
    <line x1="0.6" y1="20.4" x2="11" y2="9.5"/>
    <line x1="27.4" y1="20.4" x2="17" y2="9.5"/>
  </svg>
  <h2 class="abs contact-heading">CONTACT</h2>
  <p class="abs contact-tagline">We're always here, drop us a line!</p>

  <div class="abs field" style="left:75px;top:815px;width:126px;height:28px">Full Name</div>
  <div class="abs field" style="left:212px;top:815px;width:126px;height:28px">Email</div>
  <div class="abs field" style="left:75px;top:854px;width:126px;height:28px">Subject</div>
  <div class="abs field" style="left:75px;top:893px;width:265px;height:81px">Message</div>
  <div class="abs send">SEND</div>

  <div class="abs feature-photo" role="img" aria-label="Champagne bottle and two filled glasses with strawberries on a terrace overlooking the sea"></div>
  <p class="abs feature-quote">“The ultimate full service lifestyle club”</p>

  <div class="abs footer-rule"></div>
  <div class="abs footer-brand">VELMOR</div>
  <div class="abs footer-copy">© VELMOR 2017</div>

  <div class="abs footer-link" style="left:286px;top:1122px">About Us</div>
  <div class="abs footer-link" style="left:286px;top:1135px">Contact</div>
  <div class="abs footer-link" style="left:286px;top:1148px">Terms &amp; Conditions</div>

  <div class="abs social-mark" style="left:398px;top:1123px"></div>
  <div class="abs footer-link" style="left:417px;top:1122px">Friendly</div>
  <div class="abs social-mark" style="left:398px;top:1136px"></div>
  <div class="abs footer-link" style="left:417px;top:1135px">Chirper</div>
  <div class="abs social-mark" style="left:398px;top:1149px"></div>
  <div class="abs footer-link" style="left:417px;top:1148px">Snapline</div>

  <div class="abs newsletter-label">Subscribe to our newsletter</div>
  <div class="abs newsletter-input">Email Address</div>
  <div class="abs newsletter-ok">OK</div>

  <div class="abs address-line" style="top:1122px">18 Larchmont Ave. Fairhaven, CA 90210</div>
  <div class="abs address-line" style="top:1133px">+1 555 010 2040</div>
  <div class="abs address-line" style="top:1144px">velmorclub@mail.example</div>
</body>
</html>
```